Business cards and stationary design

We just completed the design of our new logo and we need to print new business cards and letterhead for our nonprofit. We are looking for a fresh new design that shows off our new logo. On letterhead, we must have a column on the right or left to include our Board of Directors (up to 45 names) (see attachment)

Industry/Entity Type

Non-Profit

Contact Information for Business Card

Standard business card with name, title, Company name, mailing address phone numbers, email address and website. Tagline on back "Bringing the homeless home"

Font styles to use
Sans Serif

Requirements
Must have
• include pertinent information above
• new logo
• fonts compatible with logo
• should use logo colors only
Nice to have
• tag lines

```html
<!DOCTYPE html>
<html lang="en">
<head>
<meta charset="utf-8">
<title>Hearthway Shelter Center — Business Card</title>
<link href="https://fonts.googleapis.com/css2?family=Roboto+Condensed:wght@400;700&family=Roboto:wght@400&display=swap" rel="stylesheet">
<style>
  :root {
    --stage: #e9e7e3;
    --card: #ffffff;
    --brand-blue: #1a8db0;
    --brand-teal: #1e86a6;
    --brand-yellow: #f6b82a;
    --brand-red: #e02a33;
    --on-blue: #ffffff;
    --shadow: rgba(0,0,0,0.18);
  }
  html, body {
    margin: 0;
    width: 1200px;
    height: 911px;
    overflow: hidden;
    background: var(--stage);
  }
  .stage {
    position: relative;
    width: 1200px;
    height: 911px;
  }
  .card {
    position: absolute;
    width: 560px;
    height: 320px;
    background: var(--card);
    box-shadow: 0 6px 18px var(--shadow);
    overflow: hidden;
  }
  .card--front { left: 80px; top: 110px; }
  .card--back { left: 560px; top: 480px; }

  /* Front */
  .front-band {
    position: absolute;
    inset: 0;
  }
  .identity {
    position: absolute;
    left: 40px;
    top: 120px;
    font-family: "Roboto Condensed", sans-serif;
  }
  .identity__name {
    margin: 0;
    font-size: 30px;
    font-weight: 400;
    letter-spacing: 0.5px;
    color: var(--brand-teal);
    line-height: 1;
  }
  .identity__title {
    margin: 6px 0 0;
    font-size: 20px;
    font-weight: 400;
    color: var(--brand-red);
    line-height: 1;
  }
  .mark-block {
    position: absolute;
    left: 230px;
    top: 30px;
    width: 110px;
    height: 110px;
    background: var(--brand-yellow);
  }
  .address {
    position: absolute;
    right: 22px;
    top: 62px;
    margin: 0;
    font-family: "Roboto", sans-serif;
    font-style: normal;
    font-size: 14px;
    line-height: 1.5;
    color: var(--on-blue);
    text-align: left;
  }
  .contacts {
    position: absolute;
    left: 286px;
    bottom: 26px;
    margin: 0;
    padding: 0;
    list-style: none;
    font-family: "Roboto", sans-serif;
    font-size: 13px;
    line-height: 1.65;
    color: var(--on-blue);
  }
  .contacts li {
    display: flex;
    align-items: center;
    gap: 8px;
  }
  .contacts svg { width: 12px; height: 12px; flex: none; }

  /* Back */
  .brand-lockup {
    position: absolute;
    left: 0;
    right: 0;
    top: 118px;
    display: flex;
    align-items: center;
    justify-content: center;
    gap: 14px;
  }
  .brand-lockup__square {
    width: 40px;
    height: 40px;
    background: var(--brand-blue);
  }
  .brand-lockup__name {
    margin: 0;
    font-family: "Roboto Condensed", sans-serif;
    font-size: 38px;
    font-weight: 400;
    letter-spacing: 3px;
    color: var(--brand-teal);
    text-transform: uppercase;
  }
  .brand-rule {
    position: absolute;
    left: 100px;
    right: 100px;
    top: 190px;
    height: 2px;
    background: var(--brand-red);
  }
</style>
</head>
<body>
<main class="stage">

  <section class="card card--front" aria-label="Business card front">
    <svg class="front-band" viewBox="0 0 560 320" preserveAspectRatio="none" aria-hidden="true">
      <polygon points="270,0 560,0 560,320 200,320 200,190 270,190" fill="var(--brand-blue)"/>
    </svg>

    <div class="mark-block" aria-hidden="true"></div>

    <div class="identity">
      <h1 class="identity__name">ALAN PRYCE</h1>
      <p class="identity__title">CEO/FOUNDER</p>
    </div>

    <address class="address">
      Hearthway Shelter Center<br>
      412 Alder Court<br>
      Fairbanks, Alaska 99701
    </address>

    <ul class="contacts">
      <li>
        <svg viewBox="0 0 12 12" aria-hidden="true"><path d="M2.5 1 L4.5 1 L5 3.5 L3.8 4.4 Q5 7 7.6 8.2 L8.5 7 L11 7.5 L11 9.5 Q11 11 9.5 11 Q1 10 1 2.5 Q1 1 2.5 1Z" fill="#fff"/></svg>
        555 214 0198
      </li>
      <li>
        <svg viewBox="0 0 12 12" aria-hidden="true"><rect x="1" y="2.5" width="10" height="7" fill="#fff"/><path d="M1 2.5 L6 6.5 L11 2.5" stroke="var(--brand-blue)" stroke-width="1" fill="none"/></svg>
        alan@hearthway.org
      </li>
      <li>
        <svg viewBox="0 0 12 12" aria-hidden="true"><circle cx="6" cy="6" r="5" fill="#fff"/><path d="M1 6 H11 M6 1 Q3 6 6 11 M6 1 Q9 6 6 11" stroke="var(--brand-blue)" stroke-width="0.8" fill="none"/></svg>
        www.hearthway.org
      </li>
    </ul>
  </section>

  <section class="card card--back" aria-label="Business card back">
    <div class="brand-lockup">
      <h2 class="brand-lockup__name">Hearthway Shelter</h2>
      <span class="brand-lockup__square" aria-hidden="true"></span>
    </div>
    <div class="brand-rule" aria-hidden="true"></div>
  </section>

</main>
</body>
</html>
```